RW Framewell Inc Business cards

We need business cards using our existing logo but slightly modified. Right now the logo says RW Loadbearing Masonry. We want to keep the RW part of the design, but replace the Structural Concrete portion with "FRAMEWELL". Please see the attached file.
Ideally this would be a blank template so we can add Different Names, titles, and phone numbers later.
On the one side we want only the logo and on the other side the detail. I'm attaching an example for you to see.
Please reach out with any other questions. Our address and other details will be given out once we find a design we like.

Target Market(s)

Construction Industry

```html
<!DOCTYPE html>
<html lang="en">
<head>
<meta charset="utf-8">
<title>RW Framewell Inc – Business Cards</title>
<link rel="stylesheet" href="https://fonts.googleapis.com/css2?family=Montserrat:wght@600&family=Roboto:wght@400;700&display=swap">
<style>
  :root {
    --backdrop: #5b80b9;
    --brand-blue: #2d5f9f;
    --paper: #f3f3f3;
    --ink-grey: #5a5a5a;
    --ghost: rgba(0, 0, 0, 0.06);
    --white: #ffffff;
  }
  * { margin: 0; padding: 0; box-sizing: border-box; }
  html, body {
    width: 1200px;
    height: 852px;
    overflow: hidden;
    background: var(--backdrop);
  }
  .sheet {
    position: relative;
    width: 1200px;
    height: 852px;
  }
  .card {
    position: absolute;
    top: 276px;
    width: 520px;
    height: 300px;
    border-radius: 22px;
    overflow: hidden;
  }
  .card--back { left: 60px; background: var(--brand-blue); }
  .card--front { left: 620px; background: var(--paper); }

  .wordmark {
    position: absolute;
    font-family: 'Montserrat', sans-serif;
    font-weight: 600;
    line-height: 1;
    text-align: center;
  }
  .wordmark__initials { display: block; font-size: 96px; letter-spacing: 2px; }
  .wordmark__name { display: block; font-size: 26px; letter-spacing: 7px; margin-top: 6px; }

  .card--back .wordmark {
    color: var(--white);
    left: 0; right: 0; top: 84px;
  }

  .card--front .ghost-mark {
    position: absolute;
    left: 210px; top: 10px;
    font-family: 'Montserrat', sans-serif;
    font-weight: 600;
    font-size: 200px;
    line-height: 1;
    color: var(--ghost);
  }
  .card--front .wordmark {
    color: var(--brand-blue);
    right: 30px; top: 104px;
  }
  .card--front .wordmark__initials { font-size: 78px; }
  .card--front .wordmark__name { font-size: 21px; letter-spacing: 5px; }

  .tab {
    position: absolute;
    left: -14px; top: 62px;
    width: 28px; height: 40px;
    border-radius: 0 20px 20px 0;
    background: var(--brand-blue);
  }
  .holder {
    position: absolute;
    left: 34px; top: 60px;
    font-family: 'Roboto', sans-serif;
  }
  .holder__name { font-size: 20px; font-weight: 700; color: var(--brand-blue); }
  .holder__title { font-size: 13px; color: var(--ink-grey); margin-top: 2px; }

  .contact {
    position: absolute;
    left: 34px; top: 176px;
    font-family: 'Roboto', sans-serif;
    font-size: 13px;
    color: var(--ink-grey);
    line-height: 1.4;
  }
  .contact__address {
    padding-bottom: 8px;
    border-bottom: 1px solid var(--brand-blue);
    width: 190px;
    margin-bottom: 6px;
  }
  .contact__row { display: flex; align-items: center; gap: 10px; }
  .contact__row svg { width: 11px; height: 11px; fill: var(--brand-blue); flex: none; }
</style>
</head>
<body>
<main class="sheet">
  <section class="card card--back" aria-label="Card back">
    <div class="wordmark">
      <span class="wordmark__initials">RW</span>
      <span class="wordmark__name">FRAMEWELL</span>
    </div>
  </section>

  <section class="card card--front" aria-label="Card front">
    <div class="ghost-mark" aria-hidden="true">RW</div>
    <div class="tab"></div>
    <div class="holder">
      <p class="holder__name">Jordan RW Hale</p>
      <p class="holder__title">Managing Director</p>
    </div>
    <div class="contact">
      <p class="contact__address">58 Sample Rd., Any Town,<br>Oregon, US 970123</p>
      <p class="contact__row">
        <svg viewBox="0 0 12 12" aria-hidden="true"><path d="M2 1h3l1 3-2 1a7 7 0 0 0 3 3l1-2 3 1v3c0 .6-.4 1-1 1A10 10 0 0 1 1 2c0-.6.4-1 1-1z"/></svg>
        555-010-2024
      </p>
      <p class="contact__row">
        <svg viewBox="0 0 12 12" aria-hidden="true"><path d="M1 2h10v8H1zM1.6 2.6 6 6.4l4.4-3.8"/></svg>
        jordan@framewell.example
      </p>
      <p class="contact__row">
        <svg viewBox="0 0 12 12" aria-hidden="true"><circle cx="6" cy="6" r="5"/></svg>
        www.framewell.example
      </p>
    </div>
    <div class="wordmark">
      <span class="wordmark__initials">RW</span>
      <span class="wordmark__name">FRAMEWELL</span>
    </div>
  </section>
</main>
</body>
</html>
```